Two flyers with cover pages for business services company

We need to create two double sided A4 flyers for our company. We are a company that provides professional services for businesses in Dubai, UAE.
Please note that there are two different flyers. The design must be identical. Each has a cover page. The cover page will be duplicated for both flyers.
Please note that we have added images of the Dubai skyline, clip art as place-hold/temporary images. These can be changed to be more fitting to your design. We prefer to have free images where possible but are open to purchasing Framevault images if required.
We have recommended a colour palet below. You are welcome to change some colours to be more fitting to the design. However, we must have black, white and blue and per the logo.
Target Market(s)
Businesses, entrepreneurs, professionals
Industry/Entity Type
Business Service
Requirements
Must have
- The cover page should be less crowded and more visual. So mostly images with our logo and tagline.

```html
<!DOCTYPE html>
<html lang="en">
<head>
<meta charset="utf-8">
<title>Nexora Flyers</title>
<link href="https://fonts.googleapis.com/css2?family=Signika:wght@600&family=Roboto+Condensed:wght@300;400;700&display=swap" rel="stylesheet">
<style>
:root{
  --backdrop:#dedede;
  --orange:#e27d1c;
  --navy:#142a4c;
  --blue:#1e5aa8;
  --badge:#3a78c0;
  --sky-top:#8fbde8;
  --sky-bottom:#c9dff2;
  --logo-blue:#1c9ad6;
  --ink:#222;
  --white:#fff;
}
*{box-sizing:border-box;margin:0;padding:0}
html,body{width:1200px;height:1200px;overflow:hidden}
body{background:linear-gradient(#ececec,#d2d2d2);font-family:"Roboto Condensed",sans-serif;position:relative}
.page{position:absolute;top:200px;width:566px;height:802px;background:var(--white);box-shadow:0 2px 8px rgba(0,0,0,.18);overflow:hidden}
.cover{left:26px}
.inside{left:608px}
.cover-band{position:absolute;left:0;top:0;width:100%;height:196px;background:var(--orange);display:flex;align-items:center;justify-content:center;z-index:1}
.cover-headline{font-family:"Signika",sans-serif;font-weight:600;color:var(--navy);font-size:45px;line-height:48px;text-align:center;letter-spacing:-.5px}
.cover-photo{position:absolute;left:0;top:196px;width:100%;height:606px;background:linear-gradient(var(--sky-top),var(--sky-bottom))}
.cover-figure{position:absolute;left:95px;top:176px;width:290px;height:626px;background:linear-gradient(#f7f7f7,#e9eef2);border-radius:120px 120px 0 0;opacity:.9;z-index:2}
.brand{position:absolute;display:flex;align-items:center;gap:10px;color:var(--logo-blue);font-family:"Roboto Condensed",sans-serif;font-weight:400;white-space:nowrap;z-index:3}
.brand-dot{border-radius:50%;background:var(--logo-blue)}
.cover .brand{left:328px;top:668px;font-size:50px}
.cover .brand-dot{width:50px;height:50px}
.cover-url{position:absolute;left:346px;top:740px;font-size:30px;color:var(--navy);letter-spacing:1px;z-index:3}
.inside-title{position:absolute;left:19px;top:24px;width:405px;color:var(--blue);font-weight:300;font-size:31px;line-height:34px;letter-spacing:-.3px;white-space:nowrap}
.inside .brand{left:444px;top:40px;font-size:24px;gap:7px}
.inside .brand-dot{width:20px;height:20px}
.inside-photo{position:absolute;left:0;top:101px;width:100%;height:261px;background:linear-gradient(90deg,#e8e8e8,#cfd2d6 45%,#ececec)}
.badge{position:absolute;left:32px;width:140px;height:140px;border-radius:50%;background:var(--badge);border:4px solid var(--orange);color:var(--white);display:flex;flex-direction:column;align-items:center;justify-content:center;text-align:center;font-size:15.5px;line-height:16.5px;font-weight:300;white-space:nowrap;letter-spacing:-.3px}
.badge b{font-weight:700}
.badge-price{top:344px}
.badge-guarantee{top:504px}
.offer{position:absolute;left:186px;color:var(--ink);white-space:nowrap}
.offer h2{font-weight:400;color:var(--blue);font-size:16px;margin-bottom:6px}
.offer p{font-size:14px;line-height:20px;font-weight:300}
.offer p b{font-weight:400}
.offer-network{top:380px}
.offer-best{top:456px}
.offer-list{list-style:none;font-size:12.5px;line-height:18.8px;font-weight:300}
.offer-list b{font-weight:400}
.contact-call{position:absolute;left:21px;top:682px;font-size:14px;color:#333;font-weight:300}
.contact-call b{font-weight:700}
.contact-phone{position:absolute;left:20px;top:698px;font-size:36px;color:var(--orange);font-weight:400}
.contact-line{position:absolute;top:746px;display:flex;align-items:center;gap:6px;font-size:11.5px;line-height:12.5px;color:#333;font-weight:300;white-space:nowrap}
.contact-address{left:24px}
.contact-web{left:196px;top:748px}
.director-tag{position:absolute;left:440px;top:696px;width:106px;height:62px;background:var(--orange);color:var(--white);padding:10px 0 0 12px;font-size:15px;font-weight:300;line-height:19px;white-space:nowrap}
.director-tag i{font-size:11.5px}
.director-photo{position:absolute;left:324px;top:668px;width:116px;height:116px;border-radius:50%;border:3px solid var(--orange);background:radial-gradient(circle at 50% 45%,#c7a58a,#394a66 70%)}
</style>
</head>
<body>
<section class="page cover">
  <div class="cover-band"><h1 class="cover-headline">Are you getting REAL<br>value from<br>your current sponsor?</h1></div>
  <div class="cover-photo" role="img" aria-label="Dubai skyline in soft blue haze"></div>
  <div class="cover-figure" role="img" aria-label="Smiling Emirati businessman in white kandura holding a briefcase"></div>
  <div class="brand"><span class="brand-dot"></span>Nexora</div>
  <div class="cover-url">www.nexora.ae</div>
</section>

<section class="page inside">
  <h1 class="inside-title">DO YOU NEED HELP TO INCREASE<br>YOUR SALES?</h1>
  <div class="brand"><span class="brand-dot"></span>Nexora</div>
  <div class="inside-photo" role="img" aria-label="Three businessmen reviewing documents at an office desk"></div>

  <div class="badge badge-price">AS LOW AS<br><span><b>1,500 AED</b> EASY</span>MONTHLY<br>INSTALLMENTS</div>
  <div class="badge badge-guarantee"><b>SATISFACTION<br>GUARANTEED</b>100%<br>OR YOUR<br>MONEY BACK</div>

  <div class="offer offer-network">
    <h2>Grow Your Business Through Our Extensive Network</h2>
    <p>Use our <b>3000+ Business Connections,</b><br><b>570+Decision Makers,</b> MDs, CEO's, Heads of Purchasing</p>
  </div>
  <div class="offer offer-best">
    <h2>The Best Offer in the Industry</h2>
    <ul class="offer-list">
      <li>- <b>50% off</b> your current sponsorship fees</li>
      <li>- <b>Free sponsorship for 12 months</b></li>
      <li>- Low monthly installments (starting at AED 1,500)</li>
      <li>- We can be active or silent sponsors</li>
      <li>- Unique legal structure which allows you to exit any time</li>
      <li>- Help you increase your sales</li>
      <li>- VIP introductions and connections</li>
      <li>- Legal and mediation support</li>
      <li>- We have been in this market since 2004</li>
    </ul>
  </div>

  <div class="contact-call">CALL US NOW FOR A <b>FREE CONSULTATION</b> ON</div>
  <div class="contact-phone">04 555 0192</div>
  <div class="contact-line contact-address">
    <svg width="16" height="24" viewBox="0 0 16 24"><path d="M8 1a7 7 0 0 0-7 7c0 5 7 14 7 14s7-9 7-14a7 7 0 0 0-7-7z" fill="none" stroke="#222" stroke-width="2"/><circle cx="8" cy="8" r="2.5" fill="#222"/></svg>
    <span>Meridian Business Tower,<br>24th Floor Dubai, UAE</span>
  </div>
  <div class="contact-line contact-web">
    <svg width="22" height="22" viewBox="0 0 22 22" fill="none" stroke="#222" stroke-width="1.4"><circle cx="11" cy="11" r="9.5"/><ellipse cx="11" cy="11" rx="4.5" ry="9.5"/><path d="M1.5 11h19M3 6h16M3 16h16M11 1.5v19"/></svg>
    <span>www.nexora.ae</span>
  </div>
  <div class="director-tag">Daniel Hale,<br><i>Managing Director</i></div>
  <div class="director-photo" role="img" aria-label="Portrait of the managing director in a suit"></div>
</section>
</body>
</html>
```